Redesign of business card for Cedar Ridge Mechanical

We are looking for a new design for our business cards for Cedar Ridge Mechanical. We are a plumbing & HVAC construction company, operating on the West Coast of Canada and USA. Logo attached.
Industry/Entity Type
Construction - Plumbing & HVAC
Contact Information for Business Card
Name, address, phone numbers, email, website address
Look and feel
Each slider illustrates characteristics of the customer's brand and the style your logo design should communicate.

```html
<!DOCTYPE html>
<html lang="en">
<head>
<meta charset="utf-8">
<title>Cedar Ridge Mechanical – Business Card</title>
<link href="https://fonts.googleapis.com/css2?family=Montserrat:wght@400;500;700;800&display=swap" rel="stylesheet">
<style>
  :root {
    --backdrop: #3b3b3b;
    --ink: #0a0a0a;
    --paper: #ffffff;
    --card-black: #121212;
    --mark-tone: #2a2a2a;
    --soft-ink: #1c1c1c;
  }
  * { margin: 0; padding: 0; box-sizing: border-box; }
  html, body {
    width: 1200px;
    height: 689px;
    overflow: hidden;
    background: var(--backdrop);
    font-family: "Montserrat", sans-serif;
  }
  .stage {
    position: relative;
    width: 1200px;
    height: 689px;
  }
  .card {
    position: absolute;
    top: 190px;
    width: 540px;
    height: 309px;
    border-radius: 18px;
    overflow: hidden;
  }
  /* Back side */
  .card-back {
    left: 45px;
    background: var(--card-black);
    display: flex;
    align-items: center;
    justify-content: center;
  }
  .back-brand {
    display: flex;
    align-items: center;
    gap: 16px;
  }
  .back-brand .brand-square {
    width: 34px;
    height: 34px;
    background: var(--mark-tone);
  }
  .back-brand .brand-name {
    font-weight: 700;
    font-size: 26px;
    letter-spacing: 1px;
    color: var(--mark-tone);
    text-transform: uppercase;
    line-height: 1.15;
  }
  /* Front side */
  .card-front {
    left: 615px;
    background: var(--ink);
  }
  .front-shape {
    position: absolute;
    inset: 0;
  }
  .front-brand {
    position: absolute;
    left: 62px;
    top: 118px;
    width: 180px;
    display: flex;
    align-items: center;
    gap: 10px;
  }
  .front-brand .brand-square {
    flex: none;
    width: 22px;
    height: 22px;
    background: var(--ink);
  }
  .front-brand .brand-name {
    font-weight: 800;
    font-size: 17px;
    line-height: 1.15;
    color: var(--ink);
    text-transform: uppercase;
  }
  .divider {
    position: absolute;
    left: 262px;
    top: 92px;
    width: 1.5px;
    height: 128px;
    background: var(--ink);
  }
  .contact {
    position: absolute;
    left: 282px;
    top: 78px;
    color: var(--soft-ink);
  }
  .contact .person {
    font-weight: 800;
    font-size: 21px;
    letter-spacing: 0.5px;
    color: var(--ink);
  }
  .contact .role {
    font-size: 12.5px;
    margin-bottom: 12px;
  }
  .contact-list { list-style: none; }
  .contact-list li {
    display: flex;
    align-items: center;
    gap: 7px;
    font-size: 12.5px;
    line-height: 19px;
  }
  .contact-list svg { width: 11px; height: 11px; flex: none; }
  .address {
    position: absolute;
    left: 218px;
    top: 262px;
    font-size: 12.5px;
    color: var(--soft-ink);
  }
</style>
</head>
<body>
  <main class="stage">
    <section class="card card-back" aria-label="Card back">
      <div class="back-brand">
        <span class="brand-square"></span>
        <span class="brand-name">Cedar Ridge<br>Mechanical</span>
      </div>
    </section>

    <section class="card card-front" aria-label="Card front">
      <svg class="front-shape" viewBox="0 0 540 309" preserveAspectRatio="none" aria-hidden="true">
        <path d="M92 0 L462 0 Q548 150 448 309 L58 309 Q8 150 92 0 Z" fill="var(--paper)"/>
      </svg>

      <div class="front-brand">
        <span class="brand-square"></span>
        <span class="brand-name">Cedar Ridge<br>Mechanical</span>
      </div>

      <div class="divider"></div>

      <div class="contact">
        <p class="person">DANIEL HART</p>
        <p class="role">Managing Director</p>
        <ul class="contact-list">
          <li>
            <svg viewBox="0 0 12 12"><path d="M1 3 Q6 -1 11 3 L9.5 5 L8 4 L8 5.5 L10 10 L2 10 L4 5.5 L4 4 L2.5 5 Z" fill="var(--ink)"/></svg>
            123 456 789
          </li>
          <li>
            <svg viewBox="0 0 12 12"><rect x="1" y="2.5" width="10" height="7" fill="none" stroke="var(--ink)" stroke-width="1.4"/><path d="M1 2.5 L6 6.5 L11 2.5" fill="none" stroke="var(--ink)" stroke-width="1.4"/></svg>
            info@yourgmail.com
          </li>
          <li>
            <svg viewBox="0 0 12 12"><circle cx="6" cy="6" r="5" fill="var(--ink)"/><path d="M3 4 Q5 3 6 5 Q5 7 7 8 M8 2.8 Q7 4 9 5" fill="none" stroke="var(--paper)" stroke-width="1"/></svg>
            www.yourwebsite.com
          </li>
        </ul>
      </div>

      <p class="address">Your address, City State, Zip 1234</p>
    </section>
  </main>
</body>
</html>
```